Ich habe einen Flyer für meine DJ Tätigkeit gesucht und Torben hat nach wenigen Vorschlägen bereits das richtige Design erstellt. Danach hat Torben sich mit den Feinarbeiten beschäftigt und auch gute eigene Ideen mit eingebracht. Torben hat meine Wünsche und Ideen immer sehr schnell und sehr gut umgesetzt. Ich kann den Designern nur empfehlen und werde mit den Visitenkarten im 1:1 Projekt mit ihm zusammenarbeiten. Beste Grüße DJ Ruben
Zielgruppe
Moin Moin, ich bin DJ, meine Zielgruppe sind sämtliche Altersklassen, die einen DJ für eine Party/Feier benötigen. Hauptzielgruppe sind Hochzeiten.
Meine Homepage: www.djruben-wellhausen.de.
Bilder können erstmal von meiner Homepage verwendet werden. Die Originalbilder kann ich in der Endphase zum Austauschen hochladen. Für Bilder aus Bilddatenbanken bin ich offen.
Aufgabenstellung
Ich suche für meine DJ-Tätigkeit einen Flyer (10 cm Breit und 21 cm hoch) mit einer Vorder- und einer Rückseite. Der Flyer wird hauptsächlich in einer Tanzschule in einem Flyerkasten seine Verwendung finden.
Der Flyer sollte vielleicht einen 'Eyecatcher' haben und neugierig auf meine Tätigkeit als DJ machen.
Als Texte wollte ich ein paar herausragende Merkmale aus meiner Homepage auf dem Flyer haben. Der Rest an Informationen kann dann bei Interesse auf meiner Homepage eingesehen werden. Oder vielleicht hat ja von Ihnen noch jemand nette Ideen.
Meine bevorzugten Farben sind Marineblau (siehe mein Logo). Ich mag sehr gerne Verlaufsfarben. Bin aber auch für andere Farbvorschläge offen. Das ganz Layout sollte gerne strukturiert, edel aussehen und zu meinem Stil auf meiner Webseite passen.
Ich habe mein DJ Logo und den QR-Code als Datei mit beigefügt.
Ich bin auch bei Instragram: djruben_wh
Herzliche Grüße
Ruben Teichert

```html
<!DOCTYPE html>
<html lang="de">
<head>
<meta charset="utf-8">
<title>DJ Ruben – Flyer Rückseite</title>
<link rel="stylesheet" href="https://fonts.googleapis.com/css2?family=Outfit:wght@300;400&display=swap">
<style>
  :root {
    --navy: #0b0868;
    --navy-soft: #3a2f8c;
    --ink: #15127a;
    --ink-soft: #3b3288;
    --paper: #ffffff;
  }
  * { margin: 0; padding: 0; box-sizing: border-box; }
  html, body { width: 1200px; height: 3564px; overflow: hidden; background: var(--paper); }
  body { font-family: "Outfit", sans-serif; color: var(--ink); }
  .flyer { position: relative; width: 1200px; height: 3564px; background: var(--paper); overflow: hidden; }

  .photo { position: absolute; }
  .photo--dj {
    left: 527px; top: 0; width: 673px; height: 897px;
    background: linear-gradient(120deg, #3a5fd8 0%, #8a3fd0 40%, #d83cb8 75%, #b8a8c8 100%);
  }
  .photo--wedding {
    left: 0; top: 1814px; width: 812px; height: 611px;
    background: linear-gradient(180deg, #d9cfc6 0%, #b8a89a 45%, #4b4a5a 80%, #8a6f58 100%);
  }

  .bar { position: absolute; left: 0; height: 25px; background: var(--navy); }
  .bar--top { top: 436px; width: 527px; }
  .bar--mid { top: 1056px; width: 479px; background: var(--navy-soft); }
  .bar--contact { top: 2450px; width: 424px; }
  .rail { position: absolute; left: 995px; top: 897px; width: 26px; height: 2667px; background: var(--navy); }

  .stat { position: absolute; left: 62px; font-weight: 400; line-height: 1; }
  .stat__num { font-size: 108px; letter-spacing: -2px; }
  .stat__unit { font-size: 62px; margin-left: 28px; }
  .stat__label { display: block; font-size: 64px; line-height: 68px; margin-top: 8px; }
  .stat--dj { top: 505px; }
  .stat--nye { top: 770px; }

  .acronym { position: absolute; left: 62px; top: 1112px; list-style: none; }
  .acronym li { height: 122px; display: flex; align-items: baseline; }
  .acronym__initial { width: 97px; font-size: 120px; font-weight: 300; line-height: 1; }
  .acronym__word { font-size: 84px; font-weight: 400; line-height: 1; }

  .contact { position: absolute; left: 62px; top: 2490px; color: var(--ink-soft); }
  .contact__title { font-size: 120px; font-weight: 400; line-height: 1.1; letter-spacing: -1px; }
  .contact__lines { list-style: none; margin-top: 88px; }
  .contact__lines li { font-size: 62px; font-weight: 300; height: 135.5px; line-height: 1; }
</style>
</head>
<body>
<main class="flyer">
  <div class="photo photo--dj" role="img" aria-label="Foto: DJ im Anzug mit Fliege am beleuchteten DJ-Pult mit Luftballons, rosa-blaues Licht"></div>

  <div class="bar bar--top"></div>

  <p class="stat stat--dj"><span class="stat__num">29</span><span class="stat__unit">Jahre</span><span class="stat__label">DJ Erfahrung</span></p>
  <p class="stat stat--nye"><span class="stat__num">16</span><span class="stat__unit">Jahre</span><span class="stat__label">Silvesterparty<br>Erfahrung</span></p>

  <div class="bar bar--mid"></div>

  <ul class="acronym">
    <li><span class="acronym__initial">R</span><span class="acronym__word">outiniert</span></li>
    <li><span class="acronym__initial">U</span><span class="acronym__word">nterhaltsam</span></li>
    <li><span class="acronym__initial">B</span><span class="acronym__word">egeisternd</span></li>
    <li><span class="acronym__initial">E</span><span class="acronym__word">rfahren</span></li>
    <li><span class="acronym__initial">N</span><span class="acronym__word">ahbar</span></li>
  </ul>

  <div class="photo photo--wedding" role="img" aria-label="Foto: DJ mit Brautpaar auf einer Hochzeitsfeier, Daumen hoch"></div>

  <div class="bar bar--contact"></div>

  <section class="contact">
    <h2 class="contact__title">Kontakt</h2>
    <ul class="contact__lines">
      <li>Ich bin erreichbar unter:</li>
      <li>Tel.: +49 4821 58307</li>
      <li>Mobil: +49 152 28370614</li>
      <li>Oder über die Website:</li>
      <li>www.djruben-wellhausen.de</li>
    </ul>
  </section>

  <div class="rail"></div>
</main>
</body>
</html>
```